Harbor Ledger Funds Bus card and Logo

I need a logo design and Bus card design. The fund focuses on evaluating and investing in minerals (sub-surface rights) and real estate.

Harbor ledger refers to a book of knowledge that each plebe gets when entering the Kelmont Marine Academy (my alma mater)

Target Market(s)

Investors and financial advisors

Contact Information for Business Card

Simple - perhaps a logo with a theme on book of knowledge

Logo Text

Ex Scientia Imperium

Font styles to use
Serif
Sans Serif

Colors

Designer to choose colors to be used in the design.

Requirements
Must have
• memorable logo that is relatively simple

```html
<!DOCTYPE html>
<html lang="en">
<head>
<meta charset="utf-8">
<title>Harbor Ledger Funds – Business Card</title>
<link href="https://fonts.googleapis.com/css2?family=Oswald:wght@500&family=Work+Sans:wght@400&family=Montserrat:wght@600&display=swap" rel="stylesheet">
<style>
  :root {
    --backdrop: #2a2a2a;
    --card-white: #ffffff;
    --card-navy: #143a68;
    --accent-blue: #1ea7e8;
    --ink-navy: #1b2f5e;
    --logo-white: #ffffff;
  }
  * { margin: 0; padding: 0; box-sizing: border-box; }
  html, body {
    width: 1200px;
    height: 900px;
    overflow: hidden;
    background: var(--backdrop);
  }
  .stage {
    position: relative;
    width: 1200px;
    height: 900px;
  }
  .card {
    position: absolute;
    left: 261px;
    width: 656px;
    height: 358px;
    box-shadow: 0 4px 12px rgba(0,0,0,0.45);
  }
  .card-front { top: 69px; background: var(--card-white); }
  .card-back { top: 472px; background: var(--card-navy); }

  .holder {
    position: absolute;
    right: 364px;
    top: 148px;
    text-align: right;
  }
  .holder-name {
    font-family: "Oswald", sans-serif;
    font-weight: 500;
    font-size: 37px;
    line-height: 1;
    letter-spacing: 0.5px;
    color: var(--accent-blue);
    text-transform: uppercase;
  }
  .holder-role {
    font-family: "Work Sans", sans-serif;
    font-size: 16px;
    color: var(--ink-navy);
    margin-top: 4px;
  }
  .divider {
    position: absolute;
    left: 322px;
    top: 154px;
    width: 1.5px;
    height: 53px;
    background: var(--ink-navy);
  }
  .contact-list {
    position: absolute;
    left: 348px;
    top: 149px;
    list-style: none;
    font-family: "Work Sans", sans-serif;
    font-size: 16.5px;
    color: var(--ink-navy);
  }
  .contact-list li {
    display: flex;
    align-items: center;
    height: 20.5px;
  }
  .contact-icon {
    width: 10px;
    height: 10px;
    margin-right: 8px;
    flex: none;
  }
  .address {
    position: absolute;
    left: 0;
    right: 0;
    top: 320px;
    text-align: center;
    font-family: "Work Sans", sans-serif;
    font-size: 16px;
    letter-spacing: 0.3px;
    color: var(--ink-navy);
  }

  .brand-name {
    position: absolute;
    left: 0;
    right: 0;
    top: 168px;
    text-align: center;
    font-family: "Montserrat", sans-serif;
    font-weight: 600;
    font-size: 30px;
    letter-spacing: 1px;
    color: var(--logo-white);
  }
</style>
</head>
<body>
<main class="stage">
  <section class="card card-front" aria-label="Business card front">
    <div class="holder">
      <p class="holder-name">Daniel Porter</p>
      <p class="holder-role">Director</p>
    </div>
    <span class="divider"></span>
    <ul class="contact-list">
      <li>
        <svg class="contact-icon" viewBox="0 0 10 10" aria-hidden="true">
          <path d="M2 0.8 L3.6 0.8 L4 3 L3 3.8 C3.5 5.2 4.6 6.4 6.2 7 L7 6 L9.2 6.4 L9.2 8 C9.2 8.8 8.5 9.3 7.8 9.2 C4.2 8.7 1.3 5.8 0.8 2.2 C0.7 1.5 1.2 0.8 2 0.8 Z" fill="var(--accent-blue)"/>
        </svg>
        +330 5170-4426
      </li>
      <li>
        <svg class="contact-icon" viewBox="0 0 10 10" aria-hidden="true">
          <rect x="0.7" y="2" width="8.6" height="6" rx="0.8" fill="none" stroke="var(--accent-blue)" stroke-width="1.2"/>
          <path d="M1 2.5 L5 5.5 L9 2.5" fill="none" stroke="var(--accent-blue)" stroke-width="1.2"/>
        </svg>
        info@harborledgerfunds.com
      </li>
      <li>
        <svg class="contact-icon" viewBox="0 0 10 10" aria-hidden="true">
          <circle cx="5" cy="5" r="4.2" fill="none" stroke="var(--accent-blue)" stroke-width="0.9"/>
          <ellipse cx="5" cy="5" rx="1.8" ry="4.2" fill="none" stroke="var(--accent-blue)" stroke-width="0.9"/>
          <path d="M0.8 5 H9.2 M1.5 2.8 H8.5 M1.5 7.2 H8.5" stroke="var(--accent-blue)" stroke-width="0.9"/>
        </svg>
        www.harborledgerfunds.com
      </li>
    </ul>
    <p class="address">1187 Maple Ridge Court Fair Oaks, CA 95628</p>
  </section>

  <section class="card card-back" aria-label="Business card back">
    <p class="brand-name">HARBOR LEDGER FUNDS LLC</p>
  </section>
</main>
</body>
</html>
```